Business Card Design Project

Business Card
We are rebranding with a new logo
Industry/Entity Type
Business
Contact Information for Business Card
Dennis Morvale +61 487215963 dennis@quorv.com.au P.O. Box 872 Fernlow QLD 4309
Requirements
Must have
- Logo

```html
<!DOCTYPE html>
<html lang="en">
<head>
<meta charset="utf-8">
<title>Business Card – Dennis Morvale</title>
<link rel="stylesheet" href="https://fonts.googleapis.com/css2?family=Exo+2:wght@400;500;600&display=swap">
<style>
  :root {
    --backdrop: #e6e6e6;
    --card: #ffffff;
    --blue: #1b86c4;
    --orange: #e8601c;
    --amber: #f28c1b;
    --grey: #8a8a8a;
  }
  html, body {
    margin: 0;
    width: 1200px;
    height: 898px;
    overflow: hidden;
    background: var(--backdrop);
    font-family: "Exo 2", sans-serif;
  }
  .canvas {
    width: 1200px;
    height: 898px;
    display: flex;
    align-items: center;
    justify-content: center;
  }
  .card {
    position: relative;
    width: 840px;
    height: 480px;
    background: var(--card);
    box-shadow: 0 10px 30px rgba(0,0,0,0.15);
    overflow: hidden;
  }
  .name-block {
    position: absolute;
    left: 88px;
    top: 110px;
    display: flex;
    align-items: stretch;
    gap: 22px;
  }
  .name-block .marker {
    width: 7px;
    background: var(--orange);
  }
  .name {
    margin: 0;
    color: var(--blue);
    font-weight: 500;
    font-size: 24px;
    line-height: 1.05;
    letter-spacing: 1.5px;
    text-transform: uppercase;
  }
  .contact {
    position: absolute;
    left: 116px;
    top: 292px;
    font-size: 20px;
    line-height: 1.3;
    letter-spacing: 1px;
    color: var(--grey);
  }
  .contact p { margin: 0; }
  .contact .address { margin-bottom: 22px; }
  .contact .label { color: var(--orange); font-weight: 500; }
  .brand {
    position: absolute;
    right: 80px;
    top: 120px;
    display: flex;
    align-items: center;
    gap: 16px;
  }
  .brand .dot {
    width: 44px;
    height: 44px;
    border-radius: 50%;
    background: var(--blue);
  }
  .brand-name {
    margin: 0;
    color: var(--blue);
    font-weight: 600;
    font-size: 30px;
    line-height: 1.1;
    letter-spacing: 3px;
    text-transform: uppercase;
  }
  .edge-band {
    position: absolute;
    left: 0;
    right: 0;
    bottom: 0;
    height: 16px;
    display: flex;
  }
  .edge-band .amber { flex: 40; background: var(--amber); }
  .edge-band .orange { flex: 32; background: var(--orange); }
  .edge-band .blue { flex: 28; background: var(--blue); }
</style>
</head>
<body>
<main class="canvas">
  <section class="card">
    <div class="name-block">
      <span class="marker"></span>
      <h1 class="name">Dennis<br>Morvale</h1>
    </div>

    <div class="brand">
      <span class="dot"></span>
      <p class="brand-name">Quorv<br>International</p>
    </div>

    <div class="contact">
      <p class="address">P.O. Box 872<br>Fernlow QLD 4309</p>
      <p><span class="label">Cell:</span> +61 487215963</p>
      <p><span class="label">Email:</span> dennis@quorv.com.au</p>
    </div>

    <div class="edge-band">
      <span class="amber"></span>
      <span class="orange"></span>
      <span class="blue"></span>
    </div>
  </section>
</main>
</body>
</html>
```